IT support company needs Banner Ad for the top of their quote layout template

We need a banner Ad for the top of our for quote layout template so it is sent out on all our quotes

The banner size must be 827 x 100 pixels - anything larger than 60 KB can cause upload time issues

We have attached our logo and examples of the quote page to see how it looks in the context of the whole page.

Essential elements of the banner
- Must have our logo but this can be changed to be different colours if it makes the design work better i.e. Kelmor Wave could be all in white

Colours
- Can use all of our standard colours - Orange, Black, Grey and White

Images
- As a premium IT support company we deal with people and technology so would like to see both of these Incorporated into the banner i.e. people using technology These images could be watermarked or one colour effect.

Look and Feel
- Professional, friendly, people, technology, premium

Target Market
Small business owners and managers

Industry/Entity Type

It Company

```html
<!DOCTYPE html>
<html lang="en">
<head>
<meta charset="utf-8">
<title>Kelmor Wave – Quote Banner</title>
<link rel="stylesheet" href="https://fonts.googleapis.com/css2?family=Orbitron:wght@600;800&family=Jura:wght@500&display=swap">
<style>
  :root {
    --stage-grey: #6b6b6b;
    --charcoal: #262626;
    --brand-orange: #f26109;
    --soft-orange: #f5b27f;
    --white: #ffffff;
  }
  html, body {
    margin: 0;
    width: 1200px;
    height: 1200px;
    overflow: hidden;
    background: var(--stage-grey);
  }
  .canvas {
    position: relative;
    width: 1200px;
    height: 1200px;
  }
  .banner {
    position: absolute;
    left: 35px;
    top: 533px;
    width: 1129px;
    height: 136px;
  }
  .headline {
    font-family: "Orbitron", sans-serif;
    font-weight: 800;
    font-size: 29px;
    fill: var(--brand-orange);
    letter-spacing: 0.5px;
  }
  .tagline {
    font-family: "Jura", sans-serif;
    font-weight: 500;
    font-size: 18px;
    fill: var(--white);
  }
  .brand-name {
    font-family: "Orbitron", sans-serif;
    font-weight: 600;
    font-size: 38px;
    fill: var(--white);
    letter-spacing: 1px;
  }
</style>
</head>
<body>
<div class="canvas">
  <svg class="banner" viewBox="0 0 1411 170" xmlns="http://www.w3.org/2000/svg">
    <defs>
      <linearGradient id="imageryTone" x1="0" y1="0" x2="1" y2="0">
        <stop offset="0" stop-color="#ffffff"/>
        <stop offset="0.35" stop-color="#fbe3d2"/>
        <stop offset="0.65" stop-color="var(--soft-orange)"/>
        <stop offset="1" stop-color="var(--brand-orange)"/>
      </linearGradient>
    </defs>

    <rect class="banner-base" x="0" y="0" width="1411" height="170" fill="var(--brand-orange)"/>

    <rect class="banner-imagery" x="470" y="0" width="560" height="170" fill="url(#imageryTone)"
          role="img" aria-label="Soft orange-toned image of people working with technology"/>

    <path class="curve-accent" d="M535 0 C495 40 478 120 486 170 H470 C462 120 480 40 520 0 Z" fill="var(--brand-orange)"/>
    <path class="text-panel" d="M0 0 H522 C484 40 468 120 476 170 H0 Z" fill="var(--charcoal)"/>

    <text class="headline" x="65" y="66">LOREM IPSUM</text>
    <text class="headline" x="65" y="103">DOLOR SIT AMET</text>
    <text class="tagline" x="65" y="132">consectetuer adipiscing elit</text>

    <text class="brand-name" x="1368" y="111" text-anchor="end">KELMOR WAVE</text>
  </svg>
</div>
</body>
</html>
```